Updated website design needed for Radiology Group, Pine Hollow Imaging Partners

Clean, uncluttered, updated design needed for top regional Radiology Center. Focus on personal, patient oriented design, (not clinical). Should be simple and easy to navigate, with clear CTAs. Use blues, greens and photos of people in the Central Oregon outdoors.
Uncoded, PSD design only. 2 pages: Home page and one example interior page.
reference current site: http://www.phipclinic-example.com/
Sites they like:
http://www.valescanlabs-example.com/
http://www.tbmx-example.net/handler.cfm?event=practice,main
http://www.kestrelbonecare-example.com/

Medical Imaging

2 page

Sans Serif

• Personal and patient friendly.
• Lots of white space, clean and uncluttered. Clear CTAs, such as: Patient Bill Pay, Make an Appointment, Meet Our Doctors
• Use copy and contact information from the current site.
• Use outdoor images from Central Oregon, late Winter/ Spring (snow, light colors, spring green, for example)
• Include one example interior page, either Your Exam or Meet Our Doctors
• The client likes:
• Meet Our Doctors slider section, and big, easy to navigate Information Center on www.kestrelbonecare-example.com
• The personal feel of the Your Exam section on www.valescanlabs-example.com
• Blues and Greens, outdoorsy imagery
• The client does not like:
• complex drop down menus
• clinical feel
• Do not use lorum ipsum or dummy text.
• Do not use outdoor images from other regions. Do not use Summer (hot, poolside) or Fall (red/orange leaves) images.

```html
<!DOCTYPE html>
<html lang="en">
<head>
<meta charset="utf-8">
<title>Pine Hollow Imaging Partners</title>
<link rel="stylesheet" href="https://fonts.googleapis.com/css2?family=Raleway:wght@400;500;600;700&family=Open+Sans:wght@400;600;700&display=swap">
<style>
:root{
  --navy:#0e2b63;
  --navy-deep:#0a2252;
  --row-blue:#2d4b86;
  --btn-grey:#6f7f96;
  --ink:#1b2f5c;
  --text:#5b6170;
  --muted:#8a8f99;
  --light:#f1f2f4;
  --band:#e3e5e9;
  --white:#ffffff;
}
*{margin:0;padding:0;box-sizing:border-box}
html,body{width:1200px;height:2568px;overflow:hidden;background:var(--white)}
body{position:relative;font-family:"Open Sans",sans-serif;color:var(--text)}
.abs{position:absolute}
.btn{position:absolute;background:var(--navy);color:var(--white);font:600 13px "Open Sans",sans-serif;display:flex;align-items:center;justify-content:center;letter-spacing:.3px;text-transform:uppercase}

/* header */
.site-header{position:absolute;left:0;top:0;width:1200px;height:99px;background:var(--white)}
.brand{position:absolute;left:48px;top:12px;display:flex;align-items:center;gap:12px}
.brand-mark{width:64px;height:64px;background:var(--navy)}
.brand-name{font:600 22px/1.15 "Raleway",sans-serif;color:var(--navy);width:210px}
.contact-box{position:absolute;top:20px;height:57px;background:var(--navy);color:var(--white);padding:6px 0 0 20px}
.contact-box .label{font:600 17px "Open Sans",sans-serif;display:block}
.contact-box .num{font:400 13px "Open Sans",sans-serif;display:flex;align-items:center;gap:4px;margin-top:2px}

/* nav */
.main-nav{position:absolute;left:0;top:99px;width:1200px;height:64px;background:var(--navy);display:flex;align-items:center;padding-left:48px}
.main-nav a{color:var(--white);font:400 14px "Open Sans",sans-serif;text-decoration:none;padding:0 20px;height:64px;display:flex;align-items:center;position:relative}
.main-nav a+a::before{content:"";position:absolute;left:0;top:26px;width:1px;height:13px;background:#c9d2e6}
.main-nav a.active{background:#2a4679}

/* hero */
.hero{position:absolute;left:0;top:163px;width:1200px;height:467px;background:linear-gradient(100deg,#c6ccd6 0%,#e9eef3 45%,#dfe8f1 70%,#b8cbe2 100%)}
.hero-copy{position:absolute;right:48px;top:168px;width:520px;text-align:right}
.hero-copy h1{font:700 34px/1.15 "Raleway",sans-serif;color:var(--navy)}
.hero-copy p{font:400 13px/1.75 "Open Sans",sans-serif;color:#3c4250;margin-top:10px;text-align:justify}
.dots{position:absolute;right:48px;top:450px;display:flex;gap:10px}
.dots span{width:44px;height:4px;background:var(--navy)}

/* cta band */
.cta-band{position:absolute;left:0;top:630px;width:1200px;height:171px;background:linear-gradient(90deg,#1c3a73,#2a4a85 50%,#1c3a73)}
.cta{position:absolute;top:50px;display:flex;gap:18px}
.cta-icon{width:76px;height:76px;border-radius:50%;background:var(--white);display:flex;align-items:center;justify-content:center;flex:none}
.cta h3{font:500 23px "Raleway",sans-serif;color:var(--white);border-bottom:2px solid var(--white);padding-bottom:3px;width:220px}
.cta p{font:400 12px/1.55 "Open Sans",sans-serif;color:var(--white);margin-top:6px;width:225px}

/* welcome */
.welcome{position:absolute;left:0;top:801px;width:1200px;height:274px;text-align:center}
.welcome h2{position:absolute;top:40px;width:100%;font:700 32px "Raleway",sans-serif;color:var(--navy)}
.welcome p{position:absolute;left:125px;top:98px;width:950px;font:400 12px/1.7 "Open Sans",sans-serif;color:var(--text)}

/* mri */
.mri{position:absolute;left:0;top:1075px;width:1200px;height:290px;background:linear-gradient(90deg,#e6e8ec,#f2f3f5 50%,#e4e6ea)}
.notch{position:absolute;left:588px;top:0;width:0;height:0;border-left:12px solid transparent;border-right:12px solid transparent;border-top:14px solid var(--white)}
.mri h2{position:absolute;top:66px;width:100%;text-align:center;font:700 33px "Raleway",sans-serif;color:var(--ink)}
.mri p{position:absolute;left:215px;top:126px;width:770px;text-align:center;font:400 16px/1.75 "Open Sans",sans-serif;color:#3a3f4b}

/* colonoscopy */
.vc-photo{position:absolute;left:51px;top:1441px;width:271px;height:223px;background:linear-gradient(135deg,#3c7fb0,#8cc0e0 55%,#4f8fbf)}
.vc-title{position:absolute;left:366px;top:1440px;font:600 22px "Raleway",sans-serif;color:var(--ink)}
.vc-text{position:absolute;left:366px;top:1484px;width:785px;font:400 11px/2.15 "Open Sans",sans-serif;color:var(--muted)}

/* features */
.features{position:absolute;left:0;top:1763px;width:1200px;height:445px;background:linear-gradient(90deg,#dfe2e7,#eceef1 50%,#dde1e6)}
.features h2{position:absolute;top:45px;width:100%;text-align:center;font:600 28px "Raleway",sans-serif;color:var(--ink)}
.view-all{position:absolute;left:1027px;top:82px;font:400 12px "Open Sans",sans-serif;color:var(--ink)}
.feature-row{position:absolute;left:77px;width:1043px;height:75px;background:var(--row-blue);border:2px solid #9fb0d0;color:var(--white)}
.feature-row .ficon{position:absolute;left:46px;top:13px;width:48px;height:48px;border-radius:50%;background:var(--white);display:flex;align-items:center;justify-content:center}
.feature-row .div1,.feature-row .div2{position:absolute;top:12px;width:1px;height:48px;background:#8fa3c8}
.feature-row .div1{left:131px}.feature-row .div2{left:427px}
.feature-row h3{position:absolute;left:140px;width:280px;top:0;height:71px;display:flex;align-items:center;justify-content:center;text-align:center;font:600 17px/1.2 "Raleway",sans-serif}
.feature-row p{position:absolute;left:460px;top:18px;width:420px;font:400 12px/1.5 "Open Sans",sans-serif}
.feature-row .more{position:absolute;left:902px;top:20px;width:110px;height:34px;background:var(--btn-grey);border:1px solid #aab5c6;font:400 13px "Open Sans",sans-serif;display:flex;align-items:center;justify-content:center}

/* footer */
.site-footer{position:absolute;left:0;top:2208px;width:1200px;height:262px;background:var(--white)}
.site-footer h4{position:absolute;top:38px;font:700 16px "Open Sans",sans-serif;color:var(--ink);letter-spacing:.3px}
.vline{position:absolute;top:0;width:1px;height:262px;background:#e2e4e8}
.about-photo{position:absolute;left:51px;top:82px;width:370px;height:88px;background:linear-gradient(90deg,#c9ccd2,#e8e9ec 45%,#3e4a5e)}
.foot-text{position:absolute;font:400 12px/1.5 "Open Sans",sans-serif;color:#3b404c}
.email-field{position:absolute;left:526px;top:132px;width:318px;height:36px;border:1px solid #cfd3d9;font:400 11px "Open Sans",sans-serif;color:#a4a8b0;padding:10px 14px}
.subscribe{position:absolute;left:526px;top:176px;width:318px;height:36px;background:#555a62;color:var(--white);font:600 14px "Open Sans",sans-serif;display:flex;align-items:center;justify-content:center}
.loc-item{position:absolute;left:940px;display:flex;gap:14px;font:400 13px/1.5 "Open Sans",sans-serif;color:#3b404c}
.loc-item svg{flex:none;margin-top:3px}
.bottom-bar{position:absolute;left:0;top:2470px;width:1200px;height:98px;background:var(--navy)}
.bottom-bar p{position:absolute;left:0;width:1200px;top:44px;text-align:center;font:400 12px "Open Sans",sans-serif;color:var(--white)}
.social{position:absolute;top:36px;width:30px;height:30px;border:1px solid var(--white)}
.social span{position:absolute;left:5px;top:5px;width:18px;height:18px;background:var(--white)}
</style>
</head>
<body>

<header class="site-header">
  <div class="brand">
    <div class="brand-mark"></div>
    <div class="brand-name">Pine Hollow Imaging Partners, P.C.</div>
  </div>
  <div class="contact-box" style="left:479px;width:156px"><span class="label">Medical Records:</span><span class="num"><svg width="10" height="10" viewBox="0 0 10 10"><path d="M2 1l2 2-1 1.5c.6 1.2 1.3 1.9 2.5 2.5L7 6l2 2-1.5 1.5C4.5 9 1 5.5.5 2.5z" fill="#fff"/></svg>+ (555) 210-4410</span></div>
  <div class="contact-box" style="left:678px;width:139px"><span class="label">Billing:</span><span class="num"><svg width="10" height="10" viewBox="0 0 10 10"><path d="M2 1l2 2-1 1.5c.6 1.2 1.3 1.9 2.5 2.5L7 6l2 2-1.5 1.5C4.5 9 1 5.5.5 2.5z" fill="#fff"/></svg>+ (555) 210-4425</span></div>
  <div class="contact-box" style="left:830px;width:156px"><span class="label">Scheduling:</span><span class="num"><svg width="10" height="10" viewBox="0 0 10 10"><path d="M2 1l2 2-1 1.5c.6 1.2 1.3 1.9 2.5 2.5L7 6l2 2-1.5 1.5C4.5 9 1 5.5.5 2.5z" fill="#fff"/></svg>+ (555) 210-4437</span></div>
  <div class="contact-box" style="left:1001px;width:151px"><span class="label">Main Line:</span><span class="num"><svg width="10" height="10" viewBox="0 0 10 10"><path d="M2 1l2 2-1 1.5c.6 1.2 1.3 1.9 2.5 2.5L7 6l2 2-1.5 1.5C4.5 9 1 5.5.5 2.5z" fill="#fff"/></svg>+ (555) 210-4400</span></div>
</header>

<nav class="main-nav">
  <a class="active">Home</a><a>About Us</a><a>Our Service</a><a>For Patients</a><a>Our Physicians</a><a>For Physicians</a><a>PACS &amp; Document</a><a>Appointment</a><a>Our Location</a>
</nav>

<section class="hero" role="img" aria-label="Three skiers in goggles on a chairlift with snowy mountains behind">
  <div class="hero-copy">
    <h1>Welcome to Pine Hollow Imaging Partners</h1>
    <p>Pine Hollow Imaging Partners, P.C. is a diagnostic imaging corporation providing professional services to Central and Eastern Oregon hospitals and clinics as well as state-of-the-art services in its' own outpatient imaging center.</p>
  </div>
  <div class="btn" style="left:1032px;top:335px;width:120px;height:45px">Read More</div>
  <div class="dots"><span></span><span></span><span></span></div>
</section>

<section class="cta-band">
  <div class="cta" style="left:61px">
    <div class="cta-icon"><svg width="34" height="34" viewBox="0 0 34 34"><path d="M8 6h18M8 12h18M8 6c10 0 12 12 0 12l14 12" stroke="#0e2b63" stroke-width="3.5" fill="none" stroke-linecap="round" stroke-linejoin="round"/></svg></div>
    <div><h3>Patient Bill Pay</h3><p>Lorem ipsum dolor sit amet, consecte-tur adipiscing elit, sed tempor <b>&#10140;</b></p></div>
  </div>
  <div class="cta" style="left:431px">
    <div class="cta-icon"><svg width="32" height="34" viewBox="0 0 32 34"><rect x="6" y="4" width="20" height="28" fill="none" stroke="#0e2b63" stroke-width="3"/><path d="M16 8v8M12 12h8" stroke="#0e2b63" stroke-width="2.5"/><rect x="10" y="20" width="4" height="4" fill="#0e2b63"/><rect x="18" y="20" width="4" height="4" fill="#0e2b63"/><rect x="13" y="26" width="6" height="6" fill="#0e2b63"/></svg></div>
    <div><h3>Make an Appointment</h3><p>Lorem ipsum dolor sit amet, consecte-tur adipiscing elit, sed tempor <b>&#10140;</b></p></div>
  </div>
  <div class="cta" style="left:808px">
    <div class="cta-icon"><svg width="34" height="34" viewBox="0 0 34 34"><rect x="7" y="8" width="20" height="22" rx="3" fill="none" stroke="#0e2b63" stroke-width="3"/><rect x="12" y="4" width="10" height="7" rx="2" fill="#0e2b63"/><path d="M12 20l4 4 7-8" stroke="#0e2b63" stroke-width="3" fill="none"/></svg></div>
    <div><h3>Meet Our Doctors</h3><p>Lorem ipsum dolor sit amet, consecte-tur adipiscing elit, sed tempor <b>&#10140;</b></p></div>
  </div>
</section>

<section class="welcome">
  <h2>Welcome to Pine Hollow Imaging Partners</h2>
  <p>PHIP is staffed by fellowship trained physicians with expertise in major disciplines to include mammography, ultrasound, Magnetic Resonance Imaging, Computed Tomography, Positron Emission Tomography, interventional procedures, Nuclear Medicine and general procedures which include fluoroscopy, tomography, IVP's and radiographic procedures for head, chest, abdomen and extremity examinations.</p>
  <div class="btn" style="left:539px;top:185px;width:125px;height:38px">Read More</div>
</section>

<section class="mri" role="img" aria-label="Faint background of a patient lying on an MRI scanner table">
  <div class="notch"></div>
  <h2>NEW Veltrix 3T MRI Aurora Prime</h2>
  <p>Pine Hollow MRI has acquired the most exciting innovation in MRI. Veltrix brings together the strongest magnet in Central Oregon with the 70 cm Open Bore for one powerful system.</p>
  <div class="btn" style="left:543px;top:205px;width:147px;height:38px">Read More</div>
</section>

<div class="vc-photo" role="img" aria-label="Close-up of a pen resting on a blue printed card"></div>
<h2 class="vc-title">Virtual Colonoscopy (VC),</h2>
<p class="vc-text">Virtual Colonoscopy (VC), also referred to as CT colonography, is a safe and effective exam used for colon polyp screening. The entire colon lining can be seen with VC. A computed tomography (CT) scan creates a picture of the inside of your colon. VC allows the doctor to see your colon and to take a limited look outside the colon for abnormalities of the abdomen and pelvis.<br>The main purpose of this exam is to screen for growths (polyps) in the lining of the large intestine (colon and rectum). The National Screening Council (NSC) screening guidelines recommend Virtual Colonoscopy at five year intervals for all adults age 50 and over at average risk for colon disease.</p>
<div class="btn" style="left:370px;top:1626px;width:121px;height:38px">Read More</div>

<section class="features" role="img" aria-label="Faint background of an imaging suite">
  <div class="notch" style="top:0"></div>
  <h2>Our Feature</h2>
  <span class="view-all">View All</span>
  <div class="feature-row" style="top:113px">
    <div class="ficon"><svg width="24" height="20" viewBox="0 0 24 20"><circle cx="12" cy="6" r="4" fill="#2d4b86"/><circle cx="4.5" cy="8" r="3" fill="#2d4b86"/><circle cx="19.5" cy="8" r="3" fill="#2d4b86"/><path d="M5 19c0-5 14-5 14 0z" fill="#2d4b86"/></svg></div>
    <span class="div1"></span><span class="div2"></span>
    <h3>Magnetic Resonance Imaging (MRI)</h3>
    <p>PHMRI has three convenient locations Redmond (Alder Street), PHIP on the eastside of Bend, and Ridgeview Medical Center.</p>
    <div class="more">Read More</div>
  </div>
  <div class="feature-row" style="top:209px">
    <div class="ficon"><svg width="22" height="22" viewBox="0 0 22 22"><circle cx="11" cy="11" r="9" fill="none" stroke="#2d4b86" stroke-width="3"/><circle cx="11" cy="11" r="3.5" fill="#2d4b86"/></svg></div>
    <span class="div1"></span><span class="div2"></span>
    <h3>Digital Mammography</h3>
    <p>Every 2 minutes there's a new breast cancer diagnosis made. Spend 15 minutes getting your mammogram to help guard against</p>
    <div class="more">Read More</div>
  </div>
  <div class="feature-row" style="top:305px">
    <div class="ficon"><svg width="22" height="22" viewBox="0 0 22 22"><path d="M11 2l8 5v8l-8 5-8-5V7z" fill="#2d4b86"/></svg></div>
    <span class="div1"></span><span class="div2"></span>
    <h3>Computed Tomography (CT)</h3>
    <p>PHIP now offers extended CT hours at our eastside location.<br>7:00 am – 6:30 pm.</p>
    <div class="more">Read More</div>
  </div>
</section>

<footer class="site-footer">
  <h4 style="left:56px">ABOUT US</h4>
  <div class="about-photo" role="img" aria-label="Two business people shaking hands"></div>
  <p class="foot-text" style="left:51px;top:180px;width:372px">Pine Hollow Imaging Partners, P.C. is a state-of-the-art Outpatient Imaging Center providing Professional Services to Central Oregon Hospitals and Clinics <b style="color:var(--navy)">&#10140;</b></p>
  <span class="vline" style="left:471px"></span>
  <h4 style="left:526px">NEWSLETTER SIGNUP</h4>
  <p class="foot-text" style="left:526px;top:74px;width:330px">Subscribe our newsletter to know our daily updates and offer daily updates and offersun dolor sit amet elit, sed aliqua.</p>
  <div class="email-field">Enter your Email Id</div>
  <div class="subscribe">SUBSCRIBE</div>
  <span class="vline" style="left:889px"></span>
  <h4 style="left:947px">LOCATION</h4>
  <div class="loc-item" style="top:82px"><svg width="12" height="14" viewBox="0 0 12 14"><path d="M6 0a5 5 0 0 1 5 5c0 4-5 9-5 9S1 9 1 5a5 5 0 0 1 5-5z" fill="#1b2f5c"/><circle cx="6" cy="5" r="2" fill="#fff"/></svg><span>Address Line1,<br>Address Line-2<br>Country - 123456</span></div>
  <div class="loc-item" style="top:150px"><svg width="12" height="12" viewBox="0 0 10 10"><path d="M2 1l2 2-1 1.5c.6 1.2 1.3 1.9 2.5 2.5L7 6l2 2-1.5 1.5C4.5 9 1 5.5.5 2.5z" fill="#1b2f5c"/></svg><span>Office:&nbsp; 123.456.789</span></div>
  <div class="loc-item" style="top:174px"><svg width="12" height="12" viewBox="0 0 12 12"><rect x="1" y="4" width="10" height="7" fill="#1b2f5c"/><rect x="3" y="1" width="6" height="3" fill="#1b2f5c"/></svg><span>Fax:&nbsp; 123.456.789</span></div>
  <div class="loc-item" style="top:198px"><svg width="12" height="12" viewBox="0 0 12 12"><rect x="1" y="2" width="10" height="8" fill="#1b2f5c"/><path d="M1 2l5 4 5-4" stroke="#fff" fill="none"/></svg><span>info@companyname.com</span></div>
</footer>

<div class="bottom-bar">
  <p>Copyright 2016 Company Name.&nbsp; All Rights Reserved.</p>
  <div class="social" style="left:1038px"><span></span></div>
  <div class="social" style="left:1080px"><span></span></div>
  <div class="social" style="left:1121px"><span></span></div>
</div>

</body>
</html>
```